VFX Company Business Card Design Project

The Kestrel Works is a decentralized Visual Effects Studio servicing the television and feature film industries.
Project Brief:
Take our logo that was previously designed on Pencil Harbor and make a double sided business card.
Requirements:
- Card MUST be double sided.
- Front of card MUST have the yellow part of our logo against the dark grey background.
- Back of card is completely up to the designer.
- Back of card must include the complete company logo.
Please follow these File Preparation guidelines:
http://printnook.ca/infopage?file=filetype_en&s=PrintNook_new&lang=en
Business

```html
<!DOCTYPE html>
<html lang="en">
<head>
<meta charset="utf-8">
<title>The Kestrel Works – Business Card Set</title>
<link rel="stylesheet" href="https://fonts.googleapis.com/css2?family=Jost:wght@400;500;600&display=swap">
<style>
  :root {
    --backdrop: #7b3f1f;
    --charcoal: #262626;
    --slate: #5e6b6e;
    --paper: #e9eee3;
    --sunflower: #fcc52a;
    --white: #ffffff;
    --mist: #c9cccc;
    --ink: #222222;
    --stripe: #8a8f92;
  }
  * { margin: 0; padding: 0; box-sizing: border-box; }
  html, body {
    width: 1200px; height: 733px; overflow: hidden;
    background: var(--backdrop);
    font-family: "Jost", "Futura", sans-serif;
  }
  .canvas { position: relative; width: 1200px; height: 733px; }

  .card {
    position: absolute;
    width: 525px; height: 300px;
    border-radius: 28px;
    overflow: hidden;
    box-shadow: 0 3px 8px rgba(0,0,0,.35);
  }
  .card--front   { left: 68px;  top: 43px;  background: var(--charcoal); }
  .card--contact { left: 630px; top: 47px;  background: var(--charcoal); }
  .card--light   { left: 66px;  top: 385px; background: var(--paper); }
  .card--slate   { left: 625px; top: 389px; background: var(--slate); }

  /* front: brand name in yellow */
  .front-name {
    position: absolute; inset: 0;
    display: flex; align-items: center; justify-content: center; gap: 18px;
    color: var(--sunflower);
    font-weight: 600; font-size: 44px; letter-spacing: 1px;
  }
  .front-name .dot {
    width: 34px; height: 34px; border-radius: 50%;
    background: var(--sunflower);
  }

  /* contact side */
  .contact-brand {
    position: absolute; left: 44px; top: 94px; width: 240px;
    color: var(--mist); font-weight: 600; font-size: 27px; line-height: 1;
    text-align: center;
  }
  .divider {
    position: absolute; left: 290px; top: 52px;
    width: 2px; height: 146px; background: #4a4a4a;
  }
  .person { position: absolute; left: 307px; top: 45px; color: var(--white); }
  .person__name { font-weight: 500; font-size: 20px; line-height: 1.1; }
  .person__title { font-size: 15px; color: var(--mist); margin-top: 3px; }
  .contact-list {
    position: absolute; left: 307px; top: 102px;
    list-style: none; color: var(--white); font-size: 14px;
  }
  .contact-list li { display: flex; align-items: center; gap: 7px; height: 21px; }
  .contact-list svg { width: 11px; height: 11px; fill: var(--white); flex: none; }
  .wave { position: absolute; left: 0; bottom: 0; width: 525px; height: 90px; }
  .address {
    position: absolute; left: 23px; top: 257px;
    font-size: 13px; line-height: 17px; color: var(--ink);
  }

  /* light back */
  .light-brand {
    position: absolute; left: 0; right: 0; top: 122px;
    display: flex; align-items: center; justify-content: center; gap: 16px;
    color: var(--ink); font-weight: 600; font-size: 40px;
  }
  .light-brand .dot { width: 30px; height: 30px; border-radius: 50%; background: var(--ink); }

  /* slate back */
  .slate-brand {
    position: absolute; left: 0; right: 0; top: 112px; text-align: center;
    color: var(--white); font-weight: 600; font-size: 50px;
  }

  .web {
    position: absolute; left: 0; right: 0; top: 254px; text-align: center;
    font-size: 17px; letter-spacing: 3px;
  }
  .card--light .web { color: var(--ink); top: 256px; }
  .card--slate .web { color: var(--white); }
</style>
</head>
<body>
<main class="canvas">

  <section class="card card--front" aria-label="Card front">
    <div class="front-name"><span class="dot"></span>The Kestrel Works</div>
  </section>

  <section class="card card--contact" aria-label="Card back with contact details">
    <div class="contact-brand">The Kestrel Works</div>
    <div class="divider"></div>
    <div class="person">
      <div class="person__name">Your Name</div>
      <div class="person__title">Title</div>
    </div>
    <ul class="contact-list">
      <li><svg viewBox="0 0 12 12"><path d="M2 1l2 0 1 3-1.3 1a6 6 0 0 0 3.3 3.3L8 7l3 1v2l-1 1C5 11 1 7 1 2z"/></svg>0987 654321</li>
      <li><svg viewBox="0 0 12 12"><path d="M3 1h6v3H3zM1 5h10v5H9V8H3v2H1z"/></svg>0987 654321</li>
      <li><svg viewBox="0 0 12 12"><path d="M1 3h10v7H1zM1 3l5 4 5-4" stroke="#262626" stroke-width=".8"/></svg>info@kestrelworks.com</li>
      <li><svg viewBox="0 0 12 12"><circle cx="6" cy="6" r="5"/><path d="M1 6h10M6 1v10" stroke="#262626" stroke-width=".8"/></svg>www.kestrelworks.com</li>
    </ul>
    <svg class="wave" viewBox="0 0 525 90" preserveAspectRatio="none" aria-hidden="true">
      <path d="M0 12 C120 -6 260 10 360 30 S480 42 525 28 L525 90 L0 90 Z" fill="var(--stripe)"/>
      <path d="M0 18 C120 2 260 18 360 38 S480 50 525 36 L525 90 L0 90 Z" fill="#111"/>
      <path d="M0 24 C130 10 260 26 360 46 S480 56 525 44 L525 90 L0 90 Z" fill="var(--paper)"/>
    </svg>
    <div class="address">00, Complex name<br>City, State 0042</div>
  </section>

  <section class="card card--light" aria-label="Card back, light version">
    <div class="light-brand"><span class="dot"></span>The Kestrel Works</div>
    <div class="web">www.kestrelworks.com</div>
  </section>

  <section class="card card--slate" aria-label="Card back, slate version">
    <div class="slate-brand">The Kestrel Works</div>
    <div class="web">www.kestrelworks.com</div>
  </section>

</main>
</body>
</html>
```